Website for "Bright Morrow Ltd" cleaning bsuiness

We require a website to expose our business to the local market. We want to provide background on who we are and what we do but in an easily digestible way. We clean domestic and commercial premises and want to provide a list of all of our services to potential customers. We operate out of Warrington in the UK.

We would like the website to be animated in some way so that the experience of using it is not dull or mundane. This website needs to be an extension of our company.

Target Market(s)

30 - 60 year olds for Domestic plus commercial clients

Industry/Entity Type

Cleaning Service

Coding

Coded - Design and coding required

Number of Pages Required

4 page

Font styles to use
Sans Serif

Colors
0455a3
3176b5
85acd3
cfdeed
ffffff
000000
1b1b1b
c8c8c8
757575

Requirements
Must have
• Logo which has been provided. Theme based around the logo and its colours. Simple layout to avoid confusion.
Nice to have
• Animations where possible to impress the customer.
Should not have
• any pictures of cleaning equipment, fairies, maids etc

```html
<!DOCTYPE html>
<html lang="en">
<head>
<meta charset="utf-8">
<title>Bright Morrow Ltd – Cleaning Services in Warrington</title>
<link href="https://fonts.googleapis.com/css2?family=Open+Sans:wght@400;600;700;800&display=swap" rel="stylesheet">
<style>
:root{
  --brand:#0455a3;
  --brand-mid:#3176b5;
  --accent:#1a8fd6;
  --light:#cfdeed;
  --white:#ffffff;
  --ink:#1b1b1b;
  --heading:#333333;
  --muted:#757575;
  --rule:#c8c8c8;
  --footer:#0a56a8;
  --footer-bar:#084d99;
}
*{box-sizing:border-box;margin:0;padding:0}
html,body{width:1200px;height:2731px;overflow:hidden;background:var(--white)}
body{font-family:"Open Sans",Arial,sans-serif;color:var(--muted);position:relative}
.page{position:relative;width:1200px;height:2731px;overflow:hidden}
.abs{position:absolute}
.center{left:0;right:0;text-align:center}

/* header */
.header{top:0;left:0;width:1200px;height:131px;background:var(--white)}
.brand{left:100px;top:30px;font-weight:800;font-size:34px;line-height:38px;color:var(--brand);width:200px}
.brand small{display:block;font-size:13px;font-weight:600;line-height:18px;margin-top:4px}
.contact-row{right:100px;top:28px;display:flex;gap:30px;align-items:center;font-size:13px;color:var(--ink)}
.contact-row span{display:flex;align-items:center;gap:16px}
.dot{width:36px;height:36px;border-radius:50%;background:var(--accent);display:flex;align-items:center;justify-content:center}
.nav{top:92px;right:100px;display:flex;gap:0;font-size:14px;color:var(--ink)}
.nav a{color:inherit;text-decoration:none;padding:0 29px;position:relative;height:39px}
.nav a:last-child{padding-right:0}
.nav a.active::after{content:"";position:absolute;left:18px;right:18px;bottom:0;height:3px;background:var(--accent)}

/* hero */
.hero{top:131px;left:0;width:1200px;height:485px;background:linear-gradient(180deg,#7e97b3 0%,#5f7f9f 45%,#4a6c5a 80%,#3e5a48 100%)}
.hero h1{top:189px;font-size:52px;font-weight:700;color:var(--white);letter-spacing:1px}
.hero p{top:250px;font-size:27px;font-weight:600;color:var(--white);letter-spacing:.5px}

h2{font-size:24px;font-weight:700;color:var(--heading);text-transform:uppercase}
.lead{font-size:14px;line-height:26px;color:var(--muted)}
.btn{display:inline-block;width:160px;height:40px;line-height:40px;border-radius:20px;background:var(--accent);color:var(--white);font-size:12px;font-weight:600;text-transform:uppercase;text-align:center;text-decoration:none}

/* services */
.services{top:1102px;left:100px;width:1000px;display:flex;justify-content:space-between}
.service{width:212px;text-align:center}
.service .icon{width:96px;height:96px;margin:0 auto;border-radius:50%;background:var(--accent);display:flex;align-items:center;justify-content:center}
.service h3{margin-top:28px;font-size:13px;font-weight:700;color:var(--heading)}
.service p{margin-top:15px;font-size:12px;line-height:22px}

/* who we are */
.who{top:1397px;left:0;width:1200px;height:408px;background:linear-gradient(180deg,#6c6a5f 0%,#5e5445 50%,#4a3a2e 100%)}
.who h2{color:var(--white)}

/* testimonials */
.testimonials{top:1980px;left:100px;width:1000px;display:flex;justify-content:space-between}
.quote{width:300px;position:relative}
.quote .mark{position:absolute;font-size:40px;color:var(--rule);font-family:Georgia,serif;line-height:1}
.quote .open{left:0;top:-8px}
.quote .close{right:-20px;top:52px}
.quote p{padding-left:28px;font-size:13px;line-height:23px;color:var(--ink)}
.person{display:flex;align-items:center;gap:14px;margin-top:28px}
.avatar{width:52px;height:52px;border-radius:50%;background:linear-gradient(180deg,#d9cfc6,#9aa6b4)}
.person b{display:block;font-size:13px;color:var(--brand);text-transform:uppercase}
.person span{font-size:12px;color:var(--ink)}

/* clients */
.clients{top:2316px;left:100px;width:1000px;display:flex;justify-content:space-between;align-items:center}
.client{display:flex;align-items:center;gap:8px;font-size:24px;font-weight:600;color:#9a9a9a}
.client i{width:18px;height:18px;border-radius:50%;background:#9a9a9a;display:block}

/* footer */
.footer{top:2426px;left:0;width:1200px;height:244px;background:var(--footer);color:var(--light)}
.footer h4{font-size:13px;font-weight:700;color:var(--white);text-transform:uppercase;margin-bottom:18px}
.fcol{position:absolute;top:42px;font-size:11.5px;line-height:27px}
.fcol.policy{left:104px;width:330px;line-height:23px}
.fcol ul{list-style:none}
.fcol li{display:flex;align-items:center;gap:10px}
.footer-bar{top:2670px;left:0;width:1200px;height:61px;background:var(--footer-bar);color:var(--light);font-size:11px}
.footer-bar .copy{left:104px;top:22px}
.footer-bar .social{right:100px;top:20px;display:flex;align-items:center;gap:16px}
.footer-bar .social i{width:12px;height:12px;border-radius:50%;background:var(--light);display:block}
</style>
</head>
<body>
<div class="page">

  <header class="header abs">
    <div class="brand abs">Bright Morrow<small>Professional Cleaning Service</small></div>
    <div class="contact-row abs">
      <span><i class="dot"><svg width="16" height="16" viewBox="0 0 24 24"><path fill="#fff" d="M6.6 10.8a15 15 0 0 0 6.6 6.6l2.2-2.2c.3-.3.7-.4 1-.2 1.1.4 2.3.6 3.6.6.6 0 1 .4 1 1V20c0 .6-.4 1-1 1A17 17 0 0 1 3 4c0-.6.4-1 1-1h3.5c.6 0 1 .4 1 1 0 1.3.2 2.5.6 3.6.1.3 0 .7-.2 1z"/></svg></i>( 3652 ) 480 217</span>
      <span><i class="dot"><svg width="16" height="16" viewBox="0 0 24 24"><path fill="#fff" d="M7 3h10v5H7zM4 9h16a2 2 0 0 1 2 2v6h-4v4H6v-4H2v-6a2 2 0 0 1 2-2zm4 7v3h8v-3z"/></svg></i>( 3652 ) 480 217</span>
      <span><i class="dot"><svg width="16" height="16" viewBox="0 0 24 24"><path fill="none" stroke="#fff" stroke-width="2" d="M3 6h18v12H3zM3 6l9 7 9-7"/></svg></i>info@brightmorrow.com</span>
    </div>
    <nav class="nav abs">
      <a class="active">Home</a><a>About</a><a>What we do</a><a>Who we are</a><a>Testimonials</a><a>Contact us</a>
    </nav>
  </header>

  <section class="hero abs" role="img" aria-label="Upward view of glass office towers with trees in the foreground">
    <h1 class="abs center">BRIGHT MORROW</h1>
    <p class="abs center">CLEANING SERVICES COMPANY IN WARRINGTON, UK</p>
  </section>

  <section>
    <h2 class="abs center" style="top:677px">Welcome to Bright Morrow</h2>
    <p class="lead abs" style="top:731px;left:220px;width:760px;text-align:center">Lorem Ipsum is simply dummy text of the printing and typesetting industry. Lorem Ipsum has been the industry's standard dummy text ever since the 1500s, when an unknown printer took a galley of type and scrambled it to make a type specimen book. It has survived not only five centuries, but also the leap into electronic typesetting, remaining essentially unchanged. It was popularised in the 1960s with the release of Letraset sheets containing...</p>
    <div class="abs center" style="top:872px;display:flex;justify-content:center;gap:30px">
      <a class="btn">Read more info</a><a class="btn">Contact here!</a>
    </div>
  </section>

  <section>
    <h2 class="abs center" style="top:981px">What we do</h2>
    <p class="lead abs center" style="top:1024px">Lorem Ipsum is simply dummy text of the printing and typesetting industry has been the industry's</p>
    <div class="services abs">
      <div class="service">
        <div class="icon"><svg width="48" height="48" viewBox="0 0 48 48"><path fill="#fff" d="M24 6 4 24h6v16h11V30h6v10h11V24h6z"/></svg></div>
        <h3>DOMESTIC</h3>
        <p>Lorem Ipsum is simply dummy text of the printing and typesetting industry. has been the industry...</p>
      </div>
      <div class="service">
        <div class="icon"><svg width="48" height="48" viewBox="0 0 48 48" fill="none" stroke="#fff" stroke-width="2.5"><rect x="12" y="6" width="24" height="36"/><path d="M18 13h4M26 13h4M18 20h4M26 20h4M18 27h4M26 27h4M21 42v-7h6v7"/></svg></div>
        <h3>COMMERCIAL</h3>
        <p>Lorem Ipsum is simply dummy text of the printing and typesetting industry. has been the industry...</p>
      </div>
      <div class="service">
        <div class="icon"><svg width="48" height="48" viewBox="0 0 48 48" fill="none" stroke="#fff" stroke-width="2.5"><path d="M10 8l12 14"/><path d="M20 24a7 7 0 1 0 12 8l-6-10z"/><path d="M32 36c2 2 2 5 0 6"/></svg></div>
        <h3>GARDEN</h3>
        <p>Lorem Ipsum is simply dummy text of the printing and typesetting industry. has been the industry...</p>
      </div>
      <div class="service">
        <div class="icon"><svg width="52" height="48" viewBox="0 0 52 48" fill="none" stroke="#fff" stroke-width="2.5"><path d="M4 38 18 20l10 12 6-7 14 13z"/><circle cx="34" cy="13" r="4"/></svg></div>
        <h3>LANDSCAPE</h3>
        <p>Lorem Ipsum is simply dummy text of the printing and typesetting industry. has been the industry...</p>
      </div>
    </div>
  </section>

  <section class="who abs" role="img" aria-label="Aerial view of a historic city skyline with a clock tower">
    <h2 class="abs center" style="top:102px">Who we are</h2>
    <p class="lead abs" style="top:155px;left:225px;width:750px;text-align:center;color:var(--white)">Lorem Ipsum is simply dummy text of the printing and typesetting industry. Lorem Ipsum has been the industry's standard dummy text ever since the 1500s, when an unknown printer took a galley of type and scrambled it to make a type specimen book. It has survived not only five centuries, but also the leap into electronic typesetting...</p>
    <div class="abs center" style="top:267px"><a class="btn">Read more info</a></div>
  </section>

  <section>
    <h2 class="abs center" style="top:1872px">What our client's say</h2>
    <p class="lead abs center" style="top:1912px">Lorem Ipsum is simply dummy text of the printing and typesetting industry. Lorem Ipsum has been the industry</p>
    <div class="testimonials abs">
      <div class="quote"><span class="mark open">&ldquo;</span><span class="mark close">&rdquo;</span>
        <p>Lorem Ipsum is simply dummy text of the printing and typesetting industry. Lorem Ipsum has been the industry's standard dummy text ever since...</p>
        <div class="person"><div class="avatar" role="img" aria-label="Client portrait"></div><div><b>Owen Hartley</b><span>Business man</span></div></div>
      </div>
      <div class="quote"><span class="mark open">&ldquo;</span><span class="mark close">&rdquo;</span>
        <p>Lorem Ipsum is simply dummy text of the printing and typesetting industry. Lorem Ipsum has been the industry's standard dummy text ever since...</p>
        <div class="person"><div class="avatar" role="img" aria-label="Client portrait"></div><div><b>Owen Hartley</b><span>Business man</span></div></div>
      </div>
      <div class="quote"><span class="mark open">&ldquo;</span><span class="mark close">&rdquo;</span>
        <p>Lorem Ipsum is simply dummy text of the printing and typesetting industry. Lorem Ipsum has been the industry's standard dummy text ever since...</p>
        <div class="person"><div class="avatar" role="img" aria-label="Client portrait"></div><div><b>Owen Hartley</b><span>Business man</span></div></div>
      </div>
    </div>
  </section>

  <section>
    <h2 class="abs center" style="top:2212px">Our clients</h2>
    <p class="lead abs center" style="top:2252px">Lorem Ipsum is simply dummy text of the printing and typesetting industry. Lorem Ipsum has been the industry</p>
    <div class="clients abs">
      <span class="client">Northvale</span>
      <span class="client"><i></i>Kestrel Group</span>
      <span class="client">Orbitane</span>
      <span class="client">Halden</span>
      <span class="client"><i></i>Lumenway</span>
      <span class="client">Brookline Hub</span>
    </div>
  </section>

  <footer class="footer abs">
    <div class="fcol policy"><h4>Privacy policy</h4>Lorem Ipsum is simply dummy text of the printing and typesetting industry. Lorem Ipsum has been the industry's standard dummy text ever since the 1500s Lorem Ipsum is simply dummy text of the printing and typesetting industry. Lorem Ipsum has been the industry's standard...</div>
    <div class="fcol" style="left:514px"><h4>Welcome</h4><ul><li>Home</li><li>About</li><li>What we do</li><li>Who we are</li><li>Testimonials</li></ul></div>
    <div class="fcol" style="left:701px"><h4>Information</h4><ul><li>Terms &amp; Conditions</li><li>Privacy policy</li><li>Disclaimer</li><li>Contact us</li><li>Sitemap</li></ul></div>
    <div class="fcol" style="left:909px"><h4>Contact info</h4><ul>
      <li>120 Street name, City name,</li><li>Country name : 695666</li>
      <li><svg width="12" height="12" viewBox="0 0 24 24"><path fill="#cfdeed" d="M6.6 10.8a15 15 0 0 0 6.6 6.6l2.2-2.2c.3-.3.7-.4 1-.2 1.1.4 2.3.6 3.6.6.6 0 1 .4 1 1V20c0 .6-.4 1-1 1A17 17 0 0 1 3 4c0-.6.4-1 1-1h3.5c.6 0 1 .4 1 1 0 1.3.2 2.5.6 3.6.1.3 0 .7-.2 1z"/></svg>( 3652 ) 480 217</li>
      <li><svg width="12" height="12" viewBox="0 0 24 24"><path fill="#cfdeed" d="M7 3h10v5H7zM4 9h16a2 2 0 0 1 2 2v6h-4v4H6v-4H2v-6a2 2 0 0 1 2-2zm4 7v3h8v-3z"/></svg>( 3652 ) 480 217</li>
      <li><svg width="12" height="12" viewBox="0 0 24 24"><path fill="#cfdeed" d="M2 5h20v2l-10 7L2 7zm0 4 10 7 10-7v10H2z"/></svg>info@brightmorrow.com</li>
    </ul></div>
  </footer>
  <div class="footer-bar abs">
    <span class="copy abs">© 2016. Bright Morrow. All rights reserved</span>
    <div class="social abs">Connect with our social network : <i></i><i></i><i></i><i></i><i></i></div>
  </div>

</div>
</body>
</html>
```